Upmarket Dessert Lounge needs a Business Card Design

We are an upmarket dessert lounge needing a business card to match our image.

We want something that is simple yet beautiful, feminine, classy, sophisticated and elegant. We want it to stand out and don't mind if it is bold.

The design should include our logo and colours of red or maroon with gold highlights. We don't mind if black is used.

Marlow & Quince

Target Market(s)

For those who like to indulge or treat themselves and give in to their temptations on good quality desserts.

Industry/Entity Type

Business

Requirements
Must have
• Must include our logo and our name

Marlow & Quince

M & Q

```html
<!DOCTYPE html>
<html lang="en">
<head>
<meta charset="utf-8">
<title>Marlow &amp; Quince — Business Card</title>
<link rel="stylesheet" href="https://fonts.googleapis.com/css2?family=Cinzel:wght@400;600&family=Open+Sans:wght@400;700&display=swap">
<style>
  :root {
    --maroon: #7a1318;
    --gold: #f3d3a0;
    --paper: #ffffff;
    --ink: #3a3a3a;
    --backdrop: #e9e4df;
  }
  * { margin: 0; padding: 0; box-sizing: border-box; }
  html, body { width: 1200px; height: 402px; overflow: hidden; }
  body {
    background: var(--backdrop);
    position: relative;
    font-family: "Open Sans", Arial, sans-serif;
    color: var(--ink);
  }
  .card {
    position: absolute;
    top: 56px;
    width: 512px;
    height: 292px;
    background: var(--paper);
    border-radius: 22px;
    overflow: hidden;
  }
  .card--front { left: 60px; }
  .card--back { left: 632px; }

  .edge-band {
    position: absolute; left: 0; top: 0; bottom: 0;
    width: 49px; background: var(--maroon);
  }
  .edge-rule {
    position: absolute; left: 52px; top: 0; bottom: 0;
    width: 3px; background: var(--gold);
  }

  .brand-name {
    position: absolute;
    left: 78px; top: 80px; width: 224px;
    text-align: center;
    font-family: "Cinzel", Georgia, serif;
    font-weight: 600;
    font-size: 23px;
    color: var(--maroon);
    white-space: nowrap;
  }

  .person {
    position: absolute; left: 76px; top: 172px;
    color: var(--maroon);
    font-size: 18px; font-weight: 700;
  }
  .person .title { font-weight: 400; font-size: 15px; }

  .contact-list {
    position: absolute; left: 78px; top: 210px;
    list-style: none; font-size: 12px; line-height: 17.5px;
    white-space: nowrap;
  }
  .contact-list li { display: flex; align-items: center; gap: 5px; }
  .contact-list svg { width: 10px; height: 10px; fill: var(--maroon); flex: none; }

  .divider {
    position: absolute; left: 248px; top: 250px;
    width: 1px; height: 34px; background: var(--maroon);
  }
  .address {
    position: absolute; left: 262px; top: 254px;
    font-size: 12px; line-height: 14px;
    white-space: nowrap;
  }

  .monogram {
    position: absolute; inset: 0;
    display: flex; align-items: center; justify-content: center;
    font-family: "Cinzel", Georgia, serif;
    font-weight: 600;
    font-size: 76px;
    color: var(--maroon);
  }
</style>
</head>
<body>
  <section class="card card--front">
    <div class="edge-band"></div>
    <div class="edge-rule"></div>
    <div class="brand-name">Marlow &amp; Quince</div>
    <p class="person">Your name, <span class="title">Title</span></p>
    <ul class="contact-list">
      <li><svg viewBox="0 0 10 10"><path d="M2 0.5 L4 2.5 L3 3.8 Q4.5 6 6.2 7 L7.5 6 L9.5 8 L8 9.5 Q3.5 9 0.5 2 Z"/></svg>987-654-3210</li>
      <li><svg viewBox="0 0 10 10"><rect x="2.5" y="0" width="5" height="10" rx="1"/><rect x="3.3" y="1.2" width="3.4" height="5.5" fill="#fff"/></svg>987-654-3210</li>
      <li><svg viewBox="0 0 10 10"><rect x="0" y="2" width="10" height="6.5"/><path d="M0 2 L5 6 L10 2" fill="none" stroke="#fff" stroke-width="1"/></svg>info@marlowquince.com</li>
      <li><svg viewBox="0 0 10 10"><circle cx="5" cy="5" r="4.5"/><path d="M0.5 5 H9.5 M5 0.5 V9.5 M5 0.5 Q2 5 5 9.5 M5 0.5 Q8 5 5 9.5" fill="none" stroke="#fff" stroke-width="0.7"/></svg>www.marlowquince.com</li>
    </ul>
    <div class="divider"></div>
    <p class="address">Street Name, City Name<br>State Zip Code</p>
  </section>

  <section class="card card--back">
    <div class="monogram">M &amp; Q</div>
  </section>
</body>
</html>
```